Christmas Collection Candle Label Design

Looking to update our existing Christmas Candle Collection labels. Labels should reflect the overall feel of our brand- www.kelvanoro.ca
Want to include some color elements. Holiday colors added into design but more muted/ earthy tones not vibrant colors . Metallic elements and line art botanical illustration. Fonts should be more align to brand
Scents
Holiday Tree
Candy Cane
Sugar and Spice
Joyeaux Noel

```html
<!DOCTYPE html>
<html lang="en">
<head>
<meta charset="utf-8">
<title>Sugar &amp; Spice Candle Label</title>
<link href="https://fonts.googleapis.com/css2?family=Libre+Caslon+Text:wght@400;700&family=Lato:wght@400;700&display=swap" rel="stylesheet">
<style>
  :root {
    --backdrop: #e8e1d7;
    --label-deep: #86625c;
    --label-light: #a78a83;
    --cream: #f1e8dc;
    --art-tone: #b49a92;
  }
  html, body {
    margin: 0;
    padding: 0;
    width: 1200px;
    height: 864px;
    overflow: hidden;
    background: var(--backdrop);
  }
  .canvas {
    position: relative;
    width: 1200px;
    height: 864px;
  }
  .label {
    position: absolute;
    left: 150px;
    top: 120px;
    width: 900px;
    height: 625px;
    background: linear-gradient(100deg, var(--label-deep) 0%, var(--label-deep) 45%, var(--label-light) 100%);
    color: var(--cream);
  }
  .brand {
    position: absolute;
    top: 88px;
    left: 0;
    width: 100%;
    text-align: center;
    font-family: "Libre Caslon Text", serif;
    font-size: 24px;
    letter-spacing: 1px;
  }
  .brand-tagline {
    position: absolute;
    top: 130px;
    left: 0;
    width: 100%;
    text-align: center;
    font-family: "Lato", sans-serif;
    font-size: 8px;
    letter-spacing: 2px;
  }
  .rule {
    position: absolute;
    left: 144px;
    width: 623px;
    height: 2px;
    background: var(--cream);
  }
  .rule-top { top: 188px; }
  .rule-foot-a { top: 522px; }
  .rule-foot-b { top: 583px; }
  .scent-name {
    position: absolute;
    left: 144px;
    top: 222px;
    margin: 0;
    font-family: "Libre Caslon Text", serif;
    font-weight: 400;
    font-size: 68px;
    line-height: 86px;
    letter-spacing: 1px;
  }
  .scent-name .amp { font-size: 72px; }
  .scent-note {
    position: absolute;
    left: 144px;
    top: 398px;
    font-family: "Lato", sans-serif;
    font-size: 16px;
    letter-spacing: 0.3px;
  }
  .botanical-art {
    position: absolute;
    left: 537px;
    top: 164px;
    width: 283px;
    height: 308px;
  }
  .foot-row {
    position: absolute;
    left: 144px;
    top: 541px;
    width: 623px;
    display: flex;
    justify-content: space-between;
    font-family: "Lato", sans-serif;
    font-size: 17px;
    letter-spacing: 0.3px;
  }
  .foot-row .divider { margin-left: -120px; }
</style>
</head>
<body>
<div class="canvas">
  <div class="label">
    <div class="brand">KELVANORO</div>
    <div class="brand-tagline">CLEAN PLANT BASED SCENTS</div>
    <div class="rule rule-top"></div>
    <h1 class="scent-name">SUGAR<br><span class="amp">&amp;</span>SPICE</h1>
    <div class="scent-note">MADE WITH PLANT BASED BOTANICAL</div>
    <svg class="botanical-art" role="img" aria-label="Line art illustration of lilies" viewBox="0 0 283 308">
      <defs>
        <radialGradient id="lily-tone" cx="50%" cy="50%" r="50%">
          <stop offset="0%" stop-color="#b49a92" stop-opacity="0.55"/>
          <stop offset="100%" stop-color="#b49a92" stop-opacity="0"/>
        </radialGradient>
      </defs>
      <rect width="283" height="308" fill="url(#lily-tone)"/>
    </svg>
    <div class="rule rule-foot-a"></div>
    <div class="foot-row">
      <span>13 OZ</span>
      <span class="divider">//</span>
      <span>MADE IN CANADA</span>
    </div>
    <div class="rule rule-foot-b"></div>
  </div>
</div>
</body>
</html>
```